Brivolt Technologies business card design

We need a business card designed with our new logo. it would be great if the card could communicate it is a technology based company.

Target Market(s)

system integrators

Industry/Entity Type

technology, IOT

Contact Information for Business Card

Name, designation, Address, telephone number, email address

Requirements
Must have
• logo and company name
Nice to have
• something to do with technology

```html
<!DOCTYPE html>
<html lang="en">
<head>
<meta charset="utf-8">
<title>Brivolt Technologies – Business Card</title>
<link rel="stylesheet" href="https://fonts.googleapis.com/css2?family=Inter:wght@400;500;600;700&display=swap">
<style>
  :root {
    --orange: #f7941d;
    --charcoal: #3f3f3f;
    --ink: #3a3a3a;
    --paper: #ffffff;
    --backdrop: #4b4b4b;
  }
  * { margin: 0; padding: 0; box-sizing: border-box; }
  html, body { width: 1135px; height: 1200px; overflow: hidden; }
  body {
    background: var(--backdrop);
    font-family: "Inter", Arial, sans-serif;
    position: relative;
  }
  .card {
    position: absolute;
    left: 205px;
    width: 726px;
    height: 414px;
    overflow: hidden;
    box-shadow: 0 14px 30px rgba(0,0,0,0.45);
  }
  .card--front { top: 145px; background: var(--paper); }
  .card--back { top: 641px; background: var(--charcoal); }

  /* brand name block */
  .brand {
    position: absolute;
    display: flex;
    align-items: center;
    gap: 10px;
    font-weight: 700;
  }
  .brand__mark { width: 14px; height: 14px; background: var(--orange); flex: none; }
  .brand__name { line-height: 1; }
  .brand__line1 { display: block; letter-spacing: 0.5px; }
  .brand__line2 { display: block; letter-spacing: 4px; margin-top: 4px; }

  .card--front .brand { left: 33px; top: 42px; color: var(--ink); }
  .card--front .brand__line1 { font-size: 34px; }
  .card--front .brand__line2 { font-size: 11px; }

  .card--back .brand {
    left: 50%; top: 50%;
    transform: translate(-50%, -50%);
    color: #ffffff;
    gap: 16px;
  }
  .card--back .brand__mark { width: 26px; height: 26px; }
  .card--back .brand__line1 { font-size: 62px; }
  .card--back .brand__line2 { font-size: 21px; letter-spacing: 8px; margin-top: 8px; }

  /* person */
  .person {
    position: absolute;
    right: 35px;
    top: 204px;
    text-align: right;
  }
  .person__name {
    color: var(--orange);
    font-size: 26px;
    font-weight: 600;
    letter-spacing: 0.2px;
    line-height: 1.1;
  }
  .person__role {
    color: var(--ink);
    font-size: 17px;
    font-weight: 500;
    margin-top: 4px;
  }
  .edge-tab {
    position: absolute;
    right: 0; top: 210px;
    width: 10px; height: 43px;
    background: var(--orange);
  }
  .divider {
    position: absolute;
    left: 33px; right: 35px; top: 270px;
    height: 1px; background: var(--orange);
  }

  /* contacts */
  .contacts, .address {
    position: absolute;
    top: 298px;
    list-style: none;
    color: var(--ink);
    font-size: 18px;
    line-height: 24.5px;
  }
  .contacts { left: 33px; }
  .contacts li { display: flex; align-items: center; gap: 8px; }
  .contacts svg { width: 13px; height: 13px; flex: none; }
  .address { right: 35px; text-align: right; font-style: normal; }

  .footer-band {
    position: absolute;
    left: 0; top: 374px;
    width: 726px; height: 40px;
  }
</style>
</head>
<body>

  <section class="card card--front" aria-label="Business card front">
    <div class="brand">
      <span class="brand__mark"></span>
      <span class="brand__name">
        <span class="brand__line1">BRIVOLT</span>
        <span class="brand__line2">TECHNOLOGIES</span>
      </span>
    </div>

    <div class="person">
      <div class="person__name">DANIEL VERHOEVEN</div>
      <div class="person__role">DIRECTOR</div>
    </div>
    <div class="edge-tab"></div>
    <div class="divider"></div>

    <ul class="contacts">
      <li>
        <svg viewBox="0 0 16 16" aria-hidden="true"><path d="M4 1.5 L6.2 4.6 L5 6.2 C6 8.4 7.6 10 9.8 11 L11.4 9.8 L14.5 12 L13 14.5 C7 14 2 9 1.5 3 Z" fill="none" stroke="var(--orange)" stroke-width="1.4" stroke-linejoin="round"/></svg>
        <span>(555) 318-4072</span>
      </li>
      <li>
        <svg viewBox="0 0 16 16" aria-hidden="true"><rect x="1.5" y="3.5" width="13" height="9" fill="none" stroke="var(--orange)" stroke-width="1.4"/><path d="M1.5 3.5 L8 9 L14.5 3.5" fill="none" stroke="var(--orange)" stroke-width="1.4"/></svg>
        <span>hello@brivolttech.com</span>
      </li>
      <li>
        <svg viewBox="0 0 16 16" aria-hidden="true"><circle cx="8" cy="8" r="6.5" fill="none" stroke="var(--orange)" stroke-width="1.3"/><ellipse cx="8" cy="8" rx="2.8" ry="6.5" fill="none" stroke="var(--orange)" stroke-width="1.1"/><path d="M1.5 8 H14.5 M2.5 5 H13.5 M2.5 11 H13.5" stroke="var(--orange)" stroke-width="1.1"/></svg>
        <span>brivolttech.com</span>
      </li>
    </ul>

    <address class="address">
      4127 Harbor Lane<br>
      Cedar Falls, IA 50613
    </address>

    <svg class="footer-band" viewBox="0 0 726 40" aria-hidden="true">
      <path d="M0 17 H418 C412 20 407 22.5 398 23 H0 Z" fill="var(--orange)"/>
      <path d="M726 9 H482 C452 9 440 14 422 21 C413 24.5 406 25.5 395 25.5 H0 V40 H726 Z" fill="var(--charcoal)"/>
    </svg>
  </section>

  <section class="card card--back" aria-label="Business card back">
    <div class="brand">
      <span class="brand__mark"></span>
      <span class="brand__name">
        <span class="brand__line1">BRIVOLT</span>
        <span class="brand__line2">TECHNOLOGIES</span>
      </span>
    </div>
  </section>

</body>
</html>
```